Velvet Ladle Wishes Website Design; Cupcake Business with a unique and bespoke design element

We need a website design for a new bespoke and unique business making gourmet cupcakes - but MOST IMPORTANTLY we design and handmake cupcake wrappers and toppers specifically for each client's event. We are based in Sydney, Australia. The final resulting website should be elegant yet whimsical reflecting the notion of dreams and very elegant events eg weddings and very special parties.

We want to eventually have about 5 pages, HOWEVER, this project is specifically for the first page (ie Home page) and one other only. The final required pages are: a HOME page; ABOUT US page; PHOTO GALLERY page; FLAVOUR MENU & OTHER PRODUCTS page; CONTACT & INTERNET ENQUIRY page.

We expect the HOME page to be quite elaborate, perhaps including some animation. We will be providing the text content for all the other pages, and basically they will have the same background as the home page. We are looking for a clean design that runs across each page thus giving the website a continuity that pulls it all together. We would like our logo to be included on each page.

PLEASE NOTE: We will want multiple pages worked on in the handover phase but initially we want a very concise, consistent template to limit the amount of work to prospective designers.

While we are primarily looking for the design phase to be covered by this project, we would certainly appreciate coding to be included and will take that into consideration when choosing a winner.
Updates

Hi Designers

We have added some more information to our brief - please review it.

Thanks and happy designing

Hi Designers

Please note that we have increased our Prize money to $750.00.  We hope this encourages you to participate.

Thanks and regards
Velvet Ladle Wishes

Hi Designers

We've just posted some photos to help give you an idea of what we do.  Please note our attention to detail and precision in our work.

Thanks
Velvet Ladle Wishes

Hi Designers

Please Note:  What makes us different  to any other cupcake business is that we design cupcake wrappers and toppers, unique to our client's event whether it be a wedding, a birthday party or product launch.  We consult with our client to understand themes, colours, styles etc.  We then have our designs printed, next they are cut by a specialised computerised cutting machine,  We assemble everything by hand, and usually embellish the wrapper and topper with pearls, crystals, feathers, lace, ribbons or whatever else is appropriate for the event.  All work is totally bespoke, unique and individual.  No other cupcake supplier that we know of goes to these lengths to satisfy their client's dreams.

THE WRAPPER AND TOPPER IS OUR PRIMARY SELLING POINT. 

PLEASE NOTE:- We have uploaded a new photograph which we want to be used as the main photograph on the landing page.

We have removed all previous photographs of cupcakes (except for one that we can't get rid of).

We don't want a picture of a cupcake on the landing page we want the image _D7C3239.jpg to be used for that purpose.

We have also uploaded our logo in a number of file formats as we have had requests from you for these.

Hi designers

we have a crazy busy weekend on and won't be able to make any decisions re our competition until Monday  -  sorry to keep you in suspense, just a couple more days please!

regards
Pam

Target Market(s)

Primarily women - brides, new mothers (Christenings), Event Planners, who place an emphasis on the beauty of a product rather than the cost

Industry/Entity Type

Events

Requirements
Must have
• It must have our Logo (see attached upload) on each page (our logo is a butterfly atop a cupcake resting on a spoon and our motto is "Creating Delicious Works of Art". The colours used are pale pink, blue and chocolate brown and we'd expect these colours to be repeated in the final website.
The website must have a photo gallery which we can access and add to/change as our business grows.
We need a contact page which has an "internet enquiry form".
There should be a "Menu" page describing our cupcake flavours.
The Home page must have a party/event feel to it - definitely making an enquirer want to enter further into the site.
Nice to have
• Our logo is attached below in the "uploads". One idea that we have had is to use the butterfly in the logo but start it as a caterpillar crawling on the screen; as it spins it's cocoon the words "Sweet Dreams Little Caterpillar" would appear on screen; this would incorporate the "Dreams" in our Business Name; then our logo butterfly would hatch. This encapsulates the idea of taking something plain (caterpillar/cupcake) and creating something beautiful (butterfly/OUR cupcake).
However, we are open to other design ideas.
The colours we would like to have are pale pink, blue and chocolate brown in the design.

Some websites we really admire are: www.mirabellhart.com www.ribbonglitterloaf.com.au and www.greetingsoriel.com.au
These websites have a lightness and sense of fantasy to them. They do not convey a corporate image at all, rather they make you want to be at the party.
Should not have
• No "Corporate" style.

Most Important: We already have a website which we are not happy with - that is why we are going through this exercise to replace it. That means we DO NOT want anything along the lines of our current website. We are expecting some fresh ideas for our prize money.

```html
<!DOCTYPE html>
<html lang="en">
<head>
<meta charset="utf-8">
<title>Velvet Ladle Wishes – Home</title>
<link rel="stylesheet" href="https://fonts.googleapis.com/css2?family=Open+Sans:wght@400;600;700&display=swap">
<style>
  :root {
    --page-bg: #fcdde2;
    --footer-bg: #f9abb6;
    --button-bg: #fbd6dc;
    --button-edge: #fff1f3;
    --button-text: #3a4657;
    --title-blue: #1b7ccc;
    --brand-brown: #5a3620;
    --brand-pink: #e4367f;
    --body-text: #2a2a2a;
    --photo-cream: #efe9d8;
    --photo-lilac: #d9c4d8;
    --photo-pink: #f2b8c8;
  }
  * { box-sizing: border-box; margin: 0; padding: 0; }
  html, body { width: 1200px; height: 959px; overflow: hidden; }
  body {
    position: relative;
    background: var(--page-bg);
    font-family: "Open Sans", Verdana, sans-serif;
    color: var(--body-text);
  }

  .brand {
    position: absolute;
    left: 400px; top: 150px;
    width: 360px;
    display: flex; align-items: center; justify-content: center; gap: 12px;
  }
  .brand__dot {
    width: 18px; height: 18px; border-radius: 50%;
    background: var(--brand-pink);
    flex: none;
  }
  .brand__name {
    font-size: 30px;
    font-weight: 600;
    color: var(--brand-brown);
    white-space: nowrap;
  }

  .main-nav {
    position: absolute;
    left: 881px; top: 47px;
    width: 221px;
    display: flex; flex-direction: column; gap: 12px;
  }
  .main-nav a {
    display: block;
    height: 37px; line-height: 33px;
    text-align: center;
    background: var(--button-bg);
    border: 2px solid var(--button-edge);
    border-radius: 3px;
    box-shadow: 0 0 6px rgba(230, 160, 175, 0.6);
    color: var(--button-text);
    font-size: 14px; font-weight: 700;
    letter-spacing: 1px;
    text-decoration: none;
  }

  .hero-photo {
    position: absolute;
    left: 89px; top: 272px;
    width: 523px; height: 585px;
    background:
      radial-gradient(circle at 55% 45%, var(--photo-lilac) 0 18%, transparent 32%),
      radial-gradient(circle at 20% 38%, var(--photo-pink) 0 12%, transparent 24%),
      radial-gradient(circle at 88% 40%, #f6f0d8 0 12%, transparent 24%),
      linear-gradient(180deg, #ebe2cf 0%, var(--photo-cream) 55%, #ddd6c2 100%);
  }

  .slide-pager {
    position: absolute;
    left: 422px; top: 863px;
    display: flex; gap: 10px;
    list-style: none;
  }
  .slide-pager li {
    width: 24px; height: 21px;
    background: #fff;
    font-size: 15px; font-weight: 700;
    text-align: center; line-height: 21px;
    color: #111;
  }
  .slide-pager li.is-current { background: #f3eee9; }

  .intro-heading {
    position: absolute;
    left: 633px; top: 272px;
    width: 469px; height: 66px;
    padding: 10px 0 0 13px;
    background: linear-gradient(90deg, #fdd8e2 0%, #fcc5d6 70%, #f9c0d3 100%);
    box-shadow: 0 0 8px rgba(240, 170, 190, 0.6);
  }
  .intro-heading h1 {
    font-size: 28px; font-weight: 700;
    color: var(--title-blue);
    letter-spacing: 1.5px;
    line-height: 1.1;
  }
  .intro-heading p {
    font-size: 13px; font-weight: 700;
    letter-spacing: 0.5px;
    color: #1e1e1e;
    margin-top: 1px;
  }

  .intro-copy {
    position: absolute;
    left: 645px; top: 380px;
    width: 470px;
    font-size: 14px;
    line-height: 23.4px;
    letter-spacing: 0.55px;
  }
  .intro-copy p + p { margin-top: 23.4px; }

  .site-footer {
    position: absolute;
    left: 0; top: 896px;
    width: 1200px; height: 63px;
    background: var(--footer-bg);
    border-top: 2px solid #fff;
    font-size: 14.5px;
    color: #2b2b2b;
  }
  .footer-links {
    position: absolute; left: 61px; top: 20px;
  }
  .footer-links a { color: inherit; text-decoration: none; }
  .footer-copy {
    position: absolute; right: 60px; top: 20px;
  }
</style>
</head>
<body>

  <header>
    <div class="brand">
      <span class="brand__dot"></span>
      <span class="brand__name">Velvet Ladle Wishes</span>
    </div>
    <nav class="main-nav">
      <a href="#">ABOUT US</a>
      <a href="#">FLAVOUR MENU</a>
      <a href="#">PHOTO GALLERY</a>
      <a href="#">INTERNET ENQUIRY</a>
    </nav>
  </header>

  <main>
    <div class="hero-photo" role="img" aria-label="Photograph of pastel iced cupcakes with sprinkles on a white lace cake stand"></div>
    <ol class="slide-pager">
      <li class="is-current">1</li>
      <li>2</li>
      <li>3</li>
      <li>4</li>
      <li>5</li>
    </ol>

    <div class="intro-heading">
      <h1>VELVET LADLE WISHES</h1>
      <p>CREATING DELICIOUS WORKS OF ART</p>
    </div>

    <div class="intro-copy">
      <p>Velvet Ladle Wishes is a gourmet cupcake service based in Larkfield, Sydney, specialising in artistic creations focusing heavily on design, colour, theme and most importantly taste!</p>
      <p>We handcraft the best cupcakes that you have ever tasted and they're beautiful too. Our cupcake toppers and wrappers are designed personally for your event making them a unique work of art that have the WOW factor. It's not just a cupcake - Velvet Ladle Wishes are indulgent, luxurious, chic and delicious.</p>
      <p>We are experts in selecting just the right colours and accents to match your colour palette, theme, or company logo. Everything we do is completely bespoke and we use colour/fabric swatches, floral arrangements, invitations or even just an idea to create a display at your event which will have your guests talking for weeks! We work with you every step of the way to make sure that your cupcakes will not only meet your requirements but exceed your expectations too.</p>
    </div>
  </main>

  <footer class="site-footer">
    <div class="footer-links">
      <a href="#">Products</a>&nbsp; / <a href="#">Menu Gallery</a>&nbsp; / &nbsp;<a href="#">FAQ &amp; Testimonails</a> <a href="#">Contact</a>
    </div>
    <div class="footer-copy">© Copyright Velvet Ladle Wishes 2011</div>
  </footer>

</body>
</html>
```